Events Company Needs Website Revamp

Tallwood Expos is an events company that specializes in organizing and marketing large scale consumer and trade events globally.

The new web design should provide easy classification of the events, and allow visitors to find and access the details page within 2 clicks.

There are no strict guidelines on the color theme. It just has to blend naturally with the corporate logo.
Updates

The company logo is uploaded (pdf & ai)

I came across this design which I like very much. Elegant and corporate with nice modern fonttype.

Layout wise, neat and clear. 

Please see how you can emulate the design further. Particularly, highlighting the 2 event arms (Trade/Consumer) clearly.

Target Market(s)

Consumer looking for upcoming events, B2C companies looking to participate, B2B companies looking to connect with other companies

Industry/Entity Type

It Company

Requirements
Must have
• The new design should help to achieve the following objectives:
1) Visitors should be able to easily identify and access the 2 different types of events (i.e. Trade Events and Consumer Events).
2) Visitors should be able to easily find events that interest them (e.g. filter by date, trade or consumer, category [i.e. beauty, retail, F&B, construction, etc.]).
3) Visitors should be able to access an event’s details page within 2 clicks from any page.

Main navigation to include the following links:
- About Us
- Calendar
- Consumer Events
- Trade Events
- Contact Us

Design for Three (3) pages required:
A. Homepage
- Clear differentiation and easy access to the 2 different types of events (trade and consumer)
- Featured area to showcase latest 4-5 events
- Quick way to access events calendar
- Clear call-to-action for newsletter signup
- Social media sharing widgets/buttons
- A section for latest news and press releases
- A section for featured testimonials

B. Events Listing Page
- List of links to all events
- Logos and/or photos of events
- Filter / tags to find events in a specific category (e.g. food, electronics, building & construction, etc.)

C. Events Details Page
- Photo strip to showcase event photos / brochure
- A section with event details (Date, Venue, Event Description, etc.)
- Call-to-action button to visit event website
- Call-to-action button to contact event sales team
- E.g. http://vantly-demo.com/user/brightfoxhk/brightfox-monday-2011 but with the photo strip permanently extended and of a shorter height. Event details and call-to-action buttons should also be easily seen

```html
<!DOCTYPE html>
<html lang="en">
<head>
<meta charset="utf-8">
<title>Tallwood Expos – Consumer Events</title>
<link rel="stylesheet" href="https://fonts.googleapis.com/css2?family=Roboto+Condensed:wght@400;700&family=Arimo:ital,wght@0,400;0,700;1,400&display=swap">
<style>
:root{
  --purple:#6a0d63;
  --purple-dark:#4a0746;
  --purple-light:#82187a;
  --orange:#f07a1c;
  --orange-light:#ffb12a;
  --ink:#111;
  --grey:#666;
  --rule:#ddd;
  --bar-top:#f4f4f4;
  --bar-bottom:#d2d2d2;
  --thumb:#a0527f;
}
*{box-sizing:border-box;margin:0;padding:0}
html,body{width:840px;height:1200px;overflow:hidden;background:#fff}
body{position:relative;font-family:"Arimo",sans-serif;color:var(--ink)}
.abs{position:absolute}

/* header */
.site-header{left:0;top:0;width:840px;height:125px;background:linear-gradient(180deg,var(--purple-dark) 0%,var(--purple) 55%,var(--purple-light) 100%)}
.header-rule{left:0;top:124px;width:840px;height:3px;background:var(--orange)}
.header-curve{left:0;top:126px}
.brand{left:37px;top:-55px;width:140px;height:128px;border-radius:50%;background:#fff;border:3px solid #c9a6c6;display:flex;align-items:flex-end;justify-content:center;padding-bottom:34px}
.brand-name{font-family:"Roboto Condensed",sans-serif;font-size:15px;font-weight:700;color:var(--purple)}
.nav-item{top:0;height:48px;padding-top:19px;line-height:24px;text-align:center;white-space:nowrap;font-family:"Roboto Condensed",sans-serif;font-size:19px;color:#fff;text-decoration:none;background:rgba(255,255,255,.06)}
.sub-nav{left:295px;top:48px;width:270px;height:30px;background:rgba(255,255,255,.05);font-family:"Roboto Condensed",sans-serif;font-size:11px;color:#fff}
.sub-nav span{position:absolute;top:0;line-height:30px;text-align:center;white-space:nowrap;border-right:1px solid rgba(255,255,255,.15)}

/* filter bar */
.filter-bar{left:38px;top:157px;width:767px;height:53px;background:linear-gradient(180deg,var(--bar-top),var(--bar-bottom));font-family:"Roboto Condensed",sans-serif;font-size:13px;color:#333}
.filter-bar .label{left:20px;top:0;line-height:53px}
.filter-tab{top:0;height:53px;line-height:53px;text-align:center;border-left:1px solid #c4c4c4;border-right:1px solid #fafafa;white-space:nowrap}
.filter-tab.active{background:var(--purple);color:#fff}
.filter-by{left:390px;top:0;line-height:55px;font-size:13px;letter-spacing:.3px}
.select{left:457px;top:17px;width:196px;height:21px;background:#fff;border:1px solid #bbb;font-family:"Arimo",sans-serif;font-size:10px;line-height:19px;padding-left:8px}
.select-btn{right:0;top:0;width:20px;height:19px;background:var(--purple)}
.search-btn{left:672px;top:15px;width:65px;height:22px;background:linear-gradient(#fff,#e4e4e4);border:1px solid #bbb;font-size:10px;text-align:center;line-height:20px;color:#444}

.hatch{left:38px;width:767px;height:8px;background:repeating-linear-gradient(135deg,#e0e0e0 0 2px,#fff 2px 4px)}
.page-title{left:37px;top:281px;font-family:"Roboto Condensed",sans-serif;font-size:20px;font-weight:700}

/* event card */
.event{left:0;width:840px;height:300px}
.event-logo{left:38px;top:0;width:186px;height:133px;border:1px solid #c99bc5;background:#fff;display:flex;align-items:center;justify-content:center;font-family:"Roboto Condensed",sans-serif;font-size:22px;color:#222}
.event-tools{left:38px;top:132px;width:186px;height:44px;background:var(--purple-dark);display:flex}
.event-tools span{flex:1;display:flex;align-items:center;justify-content:center;border-right:1px solid #64125f}
.visit{left:38px;top:179px;width:186px;height:22px;background:linear-gradient(var(--orange-light),var(--orange));font-family:"Roboto Condensed",sans-serif;font-weight:700;font-size:10px;color:#5a2a00;line-height:22px;padding-left:19px}
.visit svg{position:absolute;right:7px;top:7px}
.event-title{left:241px;top:-4px;font-family:"Roboto Condensed",sans-serif;font-size:20px;font-weight:700;color:var(--orange);white-space:nowrap}
.event-rule{left:241px;top:23px;width:563px;height:1px;background:var(--rule)}
.facts{left:242px;top:40px;font-family:"Roboto Condensed",sans-serif;font-size:13px;line-height:17.5px;color:var(--grey);white-space:nowrap}
.facts b{color:var(--ink);font-weight:400}
.desc{left:242px;top:123px;width:562px;font-size:9.3px;line-height:12.5px;color:var(--grey)}
.desc p+p{margin-top:12px}
.read-more{left:242px;top:200px;font-size:10px;color:var(--orange);text-decoration:underline}
.strip{left:245px;top:235px}
.thumb{position:absolute;top:0;width:57px;height:57px;background:linear-gradient(135deg,#b46a95,var(--thumb) 60%,#7d2f66)}
.thumb.light{background:linear-gradient(135deg,#eee,#c9b7c6 60%,#7a4fa0)}

/* footer */
.footer-curve{left:0;top:1010px}
.footer-rule{left:0;top:1020px;width:840px;height:3px;background:var(--orange)}
.foot-h{font-family:"Roboto Condensed",sans-serif;font-size:12px;font-weight:700;white-space:nowrap}
.foot-t{font-size:10.5px;color:var(--grey);line-height:12.5px;white-space:nowrap}
.social{left:372px;top:1087px;display:flex;gap:9px}
.social span{width:22px;height:22px;border-radius:50%;background:var(--purple-dark)}
.email{left:529px;top:1103px;width:146px;height:18px;border:1px solid #ccc;font-size:10px;font-style:italic;color:#999;line-height:16px;padding-left:6px}
.submit{left:675px;top:1103px;width:45px;height:18px;background:linear-gradient(#fff,#e2e2e2);border:1px solid #ccc;font-family:"Roboto Condensed",sans-serif;font-weight:700;font-size:8.5px;text-align:center;line-height:16px}
.top{left:766px;top:1108px;text-align:center;font-family:"Roboto Condensed",sans-serif;font-size:10px}
</style>
</head>
<body>

<header>
  <div class="abs site-header"></div>
  <div class="abs header-rule"></div>
  <svg class="abs header-curve" width="840" height="8" viewBox="0 0 840 8"><path d="M120 0 Q420 12 720 0Z" fill="var(--purple-dark)"/></svg>
  <div class="abs brand"><span class="brand-name">Tallwood Expos</span></div>
  <nav>
    <a class="abs nav-item" href="#" style="left:295px;width:86px">About Us</a>
    <a class="abs nav-item" href="#" style="left:383px;width:81px">Calendar</a>
    <a class="abs nav-item" href="#" style="left:466px;width:110px">Trade Events</a>
    <a class="abs nav-item" href="#" style="left:578px;width:138px">Consumer Events</a>
    <a class="abs nav-item" href="#" style="left:718px;width:97px">Contact Us</a>
  </nav>
  <div class="abs sub-nav">
    <span style="left:0;width:100px">Our &nbsp; Story</span>
    <span style="left:100px;width:87px">History</span>
    <span style="left:187px;width:83px">Missios</span>
  </div>
</header>

<div class="abs filter-bar">
  <span class="abs label">Show:</span>
  <span class="abs filter-tab active" style="left:66px;width:50px">All</span>
  <span class="abs filter-tab" style="left:117px;width:80px">Exibitions</span>
  <span class="abs filter-tab" style="left:198px;width:66px">Events</span>
  <span class="abs filter-tab" style="left:265px;width:86px">Roadshows</span>
  <span class="abs filter-by">FILTER BY</span>
  <div class="abs select">Food
    <span class="abs select-btn"><svg width="20" height="19"><path d="M6 8h8l-4 5z" fill="#fff"/></svg></span>
  </div>
  <div class="abs search-btn">Search</div>
</div>

<div class="abs hatch" style="top:249px"></div>
<h1 class="abs page-title">Consumer Events</h1>

<!-- event 1 -->
<article class="abs event" style="top:336px">
  <div class="abs event-logo">Vows &amp; Glow</div>
  <div class="abs event-tools">
    <span><svg width="18" height="16"><ellipse cx="9" cy="7" rx="8" ry="6" fill="#fff"/><path d="M4 11l-1 4 5-3z" fill="#fff"/></svg></span>
    <span><svg width="20" height="14"><rect x="3" y="1" width="14" height="12" fill="none" stroke="#fff" stroke-width="2"/><path d="M1 2v10M19 2v10" stroke="#fff" stroke-width="2" stroke-dasharray="2 1"/></svg></span>
    <span><svg width="20" height="16"><rect x="1" y="1" width="18" height="14" fill="none" stroke="#fff" stroke-width="1.6"/><path d="M3 13l5-6 4 4 2-2 4 4z" fill="#fff"/></svg></span>
    <span><svg width="16" height="18"><path d="M11 5l-6 7a2 2 0 0 0 3 3l7-8a3.5 3.5 0 0 0-5-5L3 10" fill="none" stroke="#fff" stroke-width="1.8"/></svg></span>
  </div>
  <a class="abs visit">Visit Site<svg width="6" height="8"><path d="M0 0l6 4-6 4z" fill="#3a1a00"/></svg></a>
  <h2 class="abs event-title">Vows &amp; Glow</h2>
  <div class="abs event-rule"></div>
  <div class="abs facts">
    <b>Venue:</b> Harbourline Convention Centre, Hall 403 - 404<br>
    <b>Date:</b> 14 - 16 August 2009 , Friday - Sunday<br>
    <b>Time:</b> 11am - 9pm<br>
    <b>Free Admission</b>
  </div>
  <div class="abs desc">
    <p>Tying the knot is an exciting time for all couples. And when it comes to planning various aspects of your special day, you'll soon realise that tying up loose ends can be quite exhausting!</p>
    <p>So whether you're scouring for that gorgeous bridal gown, exploring novel ideas, or seeking beauty packages to get you ready for your big day, you'll be inspired at our Vows &amp; Glow Event this August.</p>
  </div>
  <a class="abs read-more">Read More</a>
  <div class="abs strip">
    <svg class="abs" style="left:0;top:17px" width="14" height="24"><path d="M14 0v24L2 12z" fill="#e4e4e4"/></svg>
    <div class="thumb" style="left:21px" role="img" aria-label="Event photo: bride in white gown"></div>
    <div class="thumb" style="left:84.5px" role="img" aria-label="Event photo: bridal portrait"></div>
    <div class="thumb light" style="left:148px" role="img" aria-label="Event photo: bride with purple bouquet"></div>
    <div class="thumb" style="left:211.5px" role="img" aria-label="Event photo: bridal portrait"></div>
    <div class="thumb" style="left:275px" role="img" aria-label="Event photo: bride in white gown"></div>
    <div class="thumb" style="left:338.5px" role="img" aria-label="Event photo: bridal portrait"></div>
    <div class="thumb" style="left:402px" role="img" aria-label="Event photo: bride with bouquet"></div>
    <div class="thumb" style="left:465.5px" role="img" aria-label="Event photo: bridal portrait"></div>
    <svg class="abs" style="left:531px;top:17px" width="14" height="24"><path d="M0 0v24l12-12z" fill="#e4e4e4"/></svg>
  </div>
</article>

<div class="abs hatch" style="top:638px;height:6px"></div>

<!-- event 2 -->
<article class="abs event" style="top:679px">
  <div class="abs event-logo">Vows &amp; Glow</div>
  <div class="abs event-tools">
    <span><svg width="18" height="16"><ellipse cx="9" cy="7" rx="8" ry="6" fill="#fff"/><path d="M4 11l-1 4 5-3z" fill="#fff"/></svg></span>
    <span><svg width="20" height="14"><rect x="3" y="1" width="14" height="12" fill="none" stroke="#fff" stroke-width="2"/><path d="M1 2v10M19 2v10" stroke="#fff" stroke-width="2" stroke-dasharray="2 1"/></svg></span>
    <span><svg width="20" height="16"><rect x="1" y="1" width="18" height="14" fill="none" stroke="#fff" stroke-width="1.6"/><path d="M3 13l5-6 4 4 2-2 4 4z" fill="#fff"/></svg></span>
    <span><svg width="16" height="18"><path d="M11 5l-6 7a2 2 0 0 0 3 3l7-8a3.5 3.5 0 0 0-5-5L3 10" fill="none" stroke="#fff" stroke-width="1.8"/></svg></span>
  </div>
  <a class="abs visit">Visit Site<svg width="6" height="8"><path d="M0 0l6 4-6 4z" fill="#3a1a00"/></svg></a>
  <h2 class="abs event-title">Vows &amp; Glow</h2>
  <div class="abs event-rule"></div>
  <div class="abs facts">
    <b>Venue:</b> Harbourline Convention Centre, Hall 403 - 404<br>
    <b>Date:</b> 14 - 16 August 2009 , Friday - Sunday<br>
    <b>Time:</b> 11am - 9pm<br>
    <b>Free Admission</b>
  </div>
  <div class="abs desc">
    <p>Tying the knot is an exciting time for all couples. And when it comes to planning various aspects of your special day, you'll soon realise that tying up loose ends can be quite exhausting!</p>
    <p>So whether you're scouring for that gorgeous bridal gown, exploring novel ideas, or seeking beauty packages to get you ready for your big day, you'll be inspired at our Vows &amp; Glow Event this August.</p>
  </div>
  <a class="abs read-more">Read More</a>
  <div class="abs strip">
    <svg class="abs" style="left:0;top:17px" width="14" height="24"><path d="M14 0v24L2 12z" fill="#e4e4e4"/></svg>
    <div class="thumb" style="left:21px" role="img" aria-label="Event photo: bride in white gown"></div>
    <div class="thumb" style="left:84.5px" role="img" aria-label="Event photo: bridal portrait"></div>
    <div class="thumb light" style="left:148px" role="img" aria-label="Event photo: bride with purple bouquet"></div>
    <div class="thumb" style="left:211.5px" role="img" aria-label="Event photo: bridal portrait"></div>
    <div class="thumb" style="left:275px" role="img" aria-label="Event photo: bride in white gown"></div>
    <div class="thumb" style="left:338.5px" role="img" aria-label="Event photo: bridal portrait"></div>
    <div class="thumb" style="left:402px" role="img" aria-label="Event photo: bride with bouquet"></div>
    <div class="thumb" style="left:465.5px" role="img" aria-label="Event photo: bridal portrait"></div>
    <svg class="abs" style="left:531px;top:17px" width="14" height="24"><path d="M0 0v24l12-12z" fill="#e4e4e4"/></svg>
  </div>
</article>

<div class="abs hatch" style="top:982px;height:6px"></div>

<footer>
  <svg class="abs footer-curve" width="840" height="11" viewBox="0 0 840 11"><path d="M150 11 Q420 -4 690 11Z" fill="var(--purple-dark)"/></svg>
  <div class="abs footer-rule"></div>
  <div class="abs foot-h" style="left:37px;top:1066px">Copyright</div>
  <div class="abs foot-t" style="left:37px;top:1085px">© Tallwood Expos 2009-2010. All Rights Reserved.</div>
  <div class="abs foot-t" style="left:37px;top:1116px">• Tel: (65) 5550-1180 or (65) 5550-1181<br>• Fax: (65) 5550-1190<br>• hello@tallwoodexpos.example</div>
  <div class="abs foot-h" style="left:372px;top:1065px">Connect wit Us</div>
  <div class="abs social"><span></span><span></span><span></span><span></span></div>
  <div class="abs foot-h" style="left:529px;top:1065px">Subscribe</div>
  <div class="abs foot-t" style="left:529px;top:1082px">Get free event updates &amp; specials!</div>
  <div class="abs email">Enter Email</div>
  <div class="abs submit">SUBMIT</div>
  <div class="abs top">
    <svg width="24" height="38" viewBox="0 0 24 38"><path d="M12 0L24 14H17V38L12 32L7 38V14H0Z" fill="var(--orange)"/></svg>
    <div>Top</div>
  </div>
</footer>

</body>
</html>
```